Business Cards for a law firm

Business cards for our law firm. Use our silhoette logo and OAK PARTNERS - check our website (www.oakpartners.example)

Contact Information for Business Card

our silhouette logo, OAK PARTNERS, 800-555-0147, Dorian Pemberton, dorian@oakpartners.example

Requirements
Must have
• our silhouette logo, OAK PARTNERS, 800-555-0147, Dorian Pemberton, dorian@oakpartners.example

```html
<!DOCTYPE html>
<html lang="en">
<head>
<meta charset="utf-8">
<title>Oak Partners – Business Cards</title>
<link rel="stylesheet" href="https://fonts.googleapis.com/css2?family=Josefin+Sans:wght@300;400;600&display=swap">
<style>
  :root {
    --backdrop: #1b1b1d;
    --navy-front: #1b3170;
    --navy-back: #22306a;
    --navy-pattern: #243d85;
    --ink-light: #ffffff;
    --ink-soft: rgba(255, 255, 255, 0.82);
    --ghost: rgba(15, 28, 72, 0.5);
  }
  * { box-sizing: border-box; margin: 0; padding: 0; }
  html, body {
    width: 1200px; height: 900px; overflow: hidden;
    background: var(--backdrop);
    font-family: "Josefin Sans", sans-serif;
  }
  .canvas {
    position: relative; width: 1200px; height: 900px;
    display: flex; flex-direction: column; align-items: center; justify-content: center; gap: 36px;
  }
  .card {
    position: relative; width: 630px; height: 360px; overflow: hidden;
    box-shadow: 0 14px 30px rgba(0, 0, 0, 0.55);
  }
  .card--front { background: var(--navy-front); }
  .card--back { background: var(--navy-back); }

  .card__pattern {
    position: absolute; left: 0; top: 0; width: 100%; height: 130px;
    background: linear-gradient(180deg, var(--navy-pattern) 0%, rgba(36, 61, 133, 0) 100%);
  }
  .brand-mark {
    position: absolute; display: flex; align-items: center; gap: 10px;
    color: var(--ink-light); font-weight: 600; letter-spacing: 0.08em;
    white-space: nowrap;
  }
  .brand-mark__dot {
    flex: none; width: 12px; height: 12px; border-radius: 50%; background: var(--ink-light);
  }
  .card--front .brand-mark { left: 56px; bottom: 64px; font-size: 22px; }

  .contact-block {
    position: absolute; left: 320px; top: 80px; color: var(--ink-light);
  }
  .contact-block__name {
    font-size: 28px; font-weight: 600; font-variant: small-caps; letter-spacing: 0.09em; line-height: 1.0;
  }
  .contact-block__rule {
    width: 46px; height: 1px; background: var(--ink-soft); margin: 18px 0 14px;
  }
  .contact-block__label { font-size: 11px; color: var(--ink-soft); letter-spacing: 0.04em; }
  .contact-block__value { font-size: 17px; font-weight: 300; letter-spacing: 0.05em; margin-bottom: 8px; }
  .contact-block__email { text-transform: uppercase; font-size: 13px; letter-spacing: 0.04em; }

  .firm-name {
    position: absolute; right: 44px; bottom: 40px;
    color: var(--ink-light); font-size: 24px; font-weight: 300; letter-spacing: 0.06em;
    white-space: nowrap;
  }

  .ghost-lines {
    position: absolute; left: 150px; top: 72px; color: var(--ghost);
    font-weight: 300; line-height: 1.0; letter-spacing: 0.04em; white-space: nowrap;
  }
  .ghost-lines__big { font-size: 50px; }
  .ghost-lines__small { font-size: 22px; margin-left: 36px; }
  .card--back .brand-mark {
    left: 50%; top: 50%; transform: translate(-50%, -50%); font-size: 28px;
  }
</style>
</head>
<body>
<main class="canvas">
  <section class="card card--front">
    <div class="card__pattern" role="img" aria-label="Subtle triangle pattern fading down from the top edge"></div>
    <div class="brand-mark"><span class="brand-mark__dot"></span>OAK PARTNERS</div>
    <div class="contact-block">
      <p class="contact-block__name">Dorian<br>Pemberton</p>
      <div class="contact-block__rule"></div>
      <p class="contact-block__label">Contact no:</p>
      <p class="contact-block__value">800-555-0147</p>
      <p class="contact-block__label">E-mail</p>
      <p class="contact-block__value contact-block__email">dorian@oakpartners.example</p>
    </div>
    <p class="firm-name">OAK PARTNERS</p>
  </section>

  <section class="card card--back">
    <div class="ghost-lines" aria-hidden="true">
      <p class="ghost-lines__big">OAK PARTNERS</p>
      <p class="ghost-lines__small">OAK PARTNERS</p>
      <p class="ghost-lines__big">OAK PARTNERS</p>
      <p class="ghost-lines__small">OAK PARTNERS</p>
      <p class="ghost-lines__big">OAK PARTNERS</p>
    </div>
    <div class="brand-mark"><span class="brand-mark__dot"></span>OAK PARTNERS</div>
  </section>
</main>
</body>
</html>
```